Luxury Wine Label for New Startup Winery

We need a wine label for our new winery startup. We have worked with a local designer but do not feel the resulting label / logo have the elevation required to present our brand as a luxury wine. Our winery is called "Quailbrook Vineyards" and we are focused on extremely high quality hand crafted artisan and estate wines from the Pacific Northwest.
We would like to see designs that utilize a tree line, or other imagery that represents the "Quailbrook" part of our company name. Another interesting feature could be wood grain.
A logo will be required based on your design so please design with this in mind:
This logo should be consistent with the wine bottle label design, and should be representative of our high end exclusive wine while giving a sense of place (Oregon/ Pacific Northwest.)
I will supply an image of the design we received from our local designer, PLEASE NOTE: in general we do like wood grain and tree line concepts but feel the execution was poorly done.
ATTN: Logo design should be suitable for use on: Bottles (Red wine/rose/white wine), Bussiness cards, vehicle signage, business signage, etc
P.S.:
If you have a design that is not outside the box we are still interested in seeing it.
Label is for a burgundy style bottle with a label height of 3.5 - 4" and a width of 3.5-4"
any label <= 4"x4" and >=3.5"x3.5" will be acceptable:
HOWEVER Width should be greater than or equal to height due to the bottle format
Target Market(s)
Wine enthusiasts with adequate discretionary budgets to afford $100 bottles of wine.
Industry/Entity Type
Wine / Winery
Requirements
Must have
- A sense of luxury, a feel of exclusivity, and a theme consistent with our product and brand name
Nice to have
- Tree line, wood grain or other wood themes. Serif fonts
Should not have
- anything cheesy, off topic, hard to read script fonts or anything that makes the label hard to read from a few feet away or too busy

```html
<!DOCTYPE html>
<html lang="en">
<head>
<meta charset="utf-8">
<title>Quailbrook Vineyards — Wine Label</title>
<link href="https://fonts.googleapis.com/css2?family=Cormorant+Garamond:wght@500;600&display=swap" rel="stylesheet">
<style>
  :root {
    --backdrop: #1c2126;
    --label-ink: #2c2f33;
    --label-edge: #232629;
    --gold: #c9ad7f;
    --gold-deep: #8a7650;
    --silver: #b9bcbf;
    --silver-soft: #8d9195;
    --tree-grey: #52575d;
  }
  * { margin: 0; padding: 0; box-sizing: border-box; }
  html, body {
    width: 1200px; height: 1200px; overflow: hidden;
    background: var(--backdrop);
  }
  .canvas {
    position: relative; width: 1200px; height: 1200px;
    display: flex; align-items: center; justify-content: center;
  }
  .label {
    position: relative; width: 616px; height: 1000px;
    background: radial-gradient(ellipse at 50% 50%, #35383c 0%, var(--label-ink) 55%, var(--label-edge) 100%);
    font-family: "Cormorant Garamond", Georgia, serif;
    color: var(--silver);
    text-align: center;
  }
  .treeline {
    position: absolute; left: 0; width: 100%;
  }
  .treeline--top {
    top: 0; height: 170px;
    background: linear-gradient(90deg, var(--tree-grey) 0%, var(--gold-deep) 10%, var(--gold) 35%, #d8d2c4 55%, var(--tree-grey) 62%, var(--tree-grey) 100%);
    -webkit-mask-image: linear-gradient(180deg, transparent 0%, #000 35%, #000 80%, transparent 100%);
    mask-image: linear-gradient(180deg, transparent 0%, #000 35%, #000 80%, transparent 100%);
    opacity: .85;
  }
  .treeline--bottom {
    top: 780px; height: 220px;
    background: linear-gradient(90deg, var(--gold) 0%, var(--gold-deep) 15%, var(--gold) 35%, #d8d2c4 48%, var(--tree-grey) 58%, var(--tree-grey) 90%, var(--gold-deep) 100%);
    -webkit-mask-image: linear-gradient(180deg, transparent 0%, #000 20%, #000 70%, transparent 100%);
    mask-image: linear-gradient(180deg, transparent 0%, #000 20%, #000 70%, transparent 100%);
    opacity: .85;
  }
  .rule-top {
    position: absolute; top: 212px; left: 0; width: 100%; height: 1px;
    background: linear-gradient(90deg, transparent, var(--gold) 12%, var(--gold) 88%, transparent);
  }
  .vintage {
    position: absolute; top: 285px; width: 100%;
    font-size: 32px; font-weight: 600; color: var(--gold); letter-spacing: 1px;
  }
  .brand {
    position: absolute; top: 450px; width: 100%;
    display: flex; flex-direction: column; align-items: center;
  }
  .brand__mark {
    width: 56px; height: 56px; border-radius: 50%;
    border: 2px solid var(--silver-soft);
    margin-bottom: 34px;
  }
  .brand__name {
    font-size: 30px; font-weight: 600; letter-spacing: 12px; padding-left: 12px;
    color: var(--silver); line-height: 1;
  }
  .brand__sub {
    margin-top: 12px; font-size: 22px; font-weight: 600; letter-spacing: 12px; padding-left: 12px;
    color: var(--silver-soft); line-height: 1;
  }
  .region {
    position: absolute; top: 752px; width: 100%;
    display: flex; align-items: center; justify-content: center; gap: 16px;
    font-size: 14px; font-weight: 600; letter-spacing: 10px; color: var(--silver-soft);
  }
  .region__line { width: 50px; height: 1px; background: var(--silver-soft); }
</style>
</head>
<body>
  <main class="canvas">
    <section class="label">
      <div class="treeline treeline--top" role="img" aria-label="Gold and grey foil silhouette of a conifer tree line"></div>
      <div class="rule-top"></div>
      <div class="vintage">2025</div>
      <div class="brand">
        <span class="brand__mark"></span>
        <div class="brand__name">QUAILBROOK</div>
        <div class="brand__sub">VINEYARDS</div>
      </div>
      <div class="region">
        <span class="region__line"></span>
        <span>PACIFIC NORTHWEST</span>
        <span class="region__line"></span>
      </div>
      <div class="treeline treeline--bottom" role="img" aria-label="Mirrored gold and grey foil tree line reflection"></div>
    </section>
  </main>
</body>
</html>
```